BUSINESS CARD DESIGN

NAME- DALE VORSKIN
PHONE NUMER - 555- 714-9082
EMAIL- OFFICE@TRV-GROUNDMAKRZ.COM
BACK OF CARD- SPEACIALIZES IN LAND CLEARING, FORESTRY MUCLHING AND EXCAVATION

Contact Information for Business Card

NAME- DALE VORSKIN PHONE NUMER - 555- 714-9082 EMAIL- OFFICE@TRV-GROUNDMAKRZ.COM BACK OF CARD- SPEACIALIZES IN LAND CLEARING , MUCLHING AND EXCAVATION

```html
<!DOCTYPE html>
<html lang="en">
<head>
<meta charset="utf-8">
<title>Business Card – Travane Groundmakrz</title>
<link rel="stylesheet" href="https://fonts.googleapis.com/css2?family=Roboto:wght@300;400;700&display=swap">
<style>
  :root {
    --backdrop: #e1e5e6;
    --card: #212125;
    --accent: #f7b320;
    --ink-light: #ffffff;
  }
  * { margin: 0; padding: 0; box-sizing: border-box; }
  html, body { width: 1200px; height: 960px; overflow: hidden; }
  body {
    background: var(--backdrop);
    font-family: "Roboto", Arial, sans-serif;
    position: relative;
  }
  .card {
    position: absolute;
    left: 250px;
    width: 702px;
    height: 400px;
    background: var(--card);
    border-left: 3px solid var(--accent);
    border-bottom: 3px solid var(--accent);
  }
  .card--front { top: 60px; }
  .card--back { top: 500px; }

  .brand {
    position: absolute;
    display: flex;
    flex-direction: column;
    align-items: center;
    color: var(--accent);
    font-weight: 700;
    text-align: center;
  }
  .brand__dot {
    width: 110px; height: 110px;
    border-radius: 50%;
    background: var(--accent);
    margin-bottom: 22px;
  }
  .brand__name { font-size: 25px; letter-spacing: 1px; line-height: 1.15; }
  .brand__place { font-size: 14px; letter-spacing: 6px; margin-top: 6px; }
  .brand__phone { font-size: 13px; letter-spacing: 9px; margin-top: 6px; }

  .card--front .brand { left: 0; right: 0; top: 95px; }
  .card--back .brand { left: 15px; width: 300px; top: 88px; }
  .card--back .brand__dot { width: 100px; height: 100px; margin-bottom: 18px; }
  .card--back .brand__name { font-size: 21px; }

  .tagline {
    position: absolute;
    left: 0; right: 0; top: 356px;
    text-align: center;
    color: var(--accent);
    font-size: 15.5px;
    letter-spacing: 0.4px;
  }

  .divider {
    position: absolute;
    left: 350px; top: 71px;
    width: 1px; height: 260px;
    background: var(--accent);
    opacity: 0.7;
  }
  .person {
    position: absolute;
    left: 392px; top: 125px;
    font-size: 39px;
    color: var(--accent);
    letter-spacing: 1px;
    white-space: nowrap;
  }
  .person__first { font-weight: 700; }
  .person__last { font-weight: 300; }

  .contacts {
    position: absolute;
    left: 393px; top: 194px;
    list-style: none;
  }
  .contacts li {
    display: flex; align-items: center;
    height: 22px;
    color: var(--ink-light);
    font-size: 15.5px;
    letter-spacing: 0.8px;
  }
  .contacts svg { width: 16px; height: 16px; margin-right: 9px; flex: none; }
</style>
</head>
<body>
  <section class="card card--front">
    <div class="brand">
      <div class="brand__dot"></div>
      <div class="brand__name">TRAVANE GROUNDMAKRZ LLC</div>
      <div class="brand__place">HAWAII</div>
      <div class="brand__phone">555-714-9082</div>
    </div>
    <p class="tagline">SPEACIALIZES IN LAND CLEARING , MUCLHING AND EXCAVATION</p>
  </section>

  <section class="card card--back">
    <div class="brand">
      <div class="brand__dot"></div>
      <div class="brand__name">TRAVANE GROUNDMAKRZ LLC</div>
      <div class="brand__place">HAWAII</div>
      <div class="brand__phone">555-714-9082</div>
    </div>
    <div class="divider"></div>
    <h1 class="person"><span class="person__first">DALE</span> <span class="person__last">VORSKIN</span></h1>
    <ul class="contacts">
      <li>
        <svg viewBox="0 0 16 16" aria-hidden="true"><path fill="#f7b320" d="M3.2 1.5l2.3 2.6-1.2 1.8c.9 2 2.5 3.6 4.5 4.6l1.8-1.2 2.6 2.3-1.3 2.4C6.5 13.5 2.5 9.5 1 4.1z"/><path d="M9.5 2.5a4 4 0 014 4M9.5 0.8a5.7 5.7 0 015.7 5.7" stroke="#f7b320" stroke-width="1.2" fill="none"/></svg>
        555- 714-9082
      </li>
      <li>
        <svg viewBox="0 0 16 16" aria-hidden="true"><circle cx="8" cy="8" r="7" fill="#f7b320"/><path d="M1 8h14M8 1c-3 3.5-3 10.5 0 14M8 1c3 3.5 3 10.5 0 14" stroke="#212125" stroke-width="1" fill="none"/></svg>
        WWW.TRV-GROUNDMAKRZ.COM
      </li>
      <li>
        <svg viewBox="0 0 16 16" aria-hidden="true"><rect x="1" y="4" width="14" height="10" fill="#f7b320"/><path d="M1 4l7 6 7-6" stroke="#212125" stroke-width="1" fill="none"/></svg>
        OFFICE@TRV-GROUNDMAKRZ.COM
      </li>
    </ul>
  </section>
</body>
</html>
```